Harborline Auto LLC

Car Dealer Customer Service
Address: 2874 Cresthaven Road, Larkmont, OH 45999
web: www.harborlineautoxq.net
email: harborlineautoxq@mailnest.example
Phone: (555) 555-0148
Phone: (555) 555-0173

```html
<!DOCTYPE html>
<html lang="en">
<head>
<meta charset="utf-8">
<title>Harborline Auto – Business Card</title>
<link href="https://fonts.googleapis.com/css2?family=Montserrat:wght@500;800&display=swap" rel="stylesheet">
<style>
  :root {
    --brand-blue: #1f78b0;
    --band-blue: #2892cf;
    --accent-gold: #ecb03f;
    --ink: #1c1c1c;
    --card: #ffffff;
    --backdrop: #2b2b2b;
  }
  * { margin: 0; padding: 0; box-sizing: border-box; }
  html, body { width: 1200px; height: 960px; overflow: hidden; }
  body {
    background: var(--backdrop);
    font-family: "Montserrat", sans-serif;
    position: relative;
  }
  .card {
    position: absolute;
    left: 250px;
    width: 700px;
    height: 400px;
    background: var(--card);
    border-radius: 22px;
    overflow: hidden;
    box-shadow: 0 10px 30px rgba(0,0,0,.5);
  }
  .card--front { top: 50px; }
  .card--back { top: 510px; }

  .brand {
    position: absolute;
    display: flex;
    align-items: center;
    gap: 14px;
  }
  .brand__dot {
    width: 46px; height: 46px;
    border-radius: 50%;
    background: var(--accent-gold);
    flex: none;
  }
  .brand__name {
    font-weight: 800;
    color: var(--brand-blue);
    font-size: 30px;
    letter-spacing: .5px;
    text-transform: uppercase;
    white-space: nowrap;
  }
  .card--front .brand { left: 50%; top: 50%; transform: translate(-50%, -50%); }
  .card--back .brand { left: 30px; top: 112px; gap: 12px; }
  .card--back .brand__name { font-size: 22px; }
  .card--back .brand__dot { width: 34px; height: 34px; }

  .divider {
    position: absolute;
    left: 345px; top: 48px;
    width: 2px; height: 162px;
    background: var(--band-blue);
  }
  .contact {
    position: absolute;
    left: 365px; top: 40px;
    color: var(--ink);
    font-weight: 500;
    font-size: 14px;
    line-height: 1.45;
  }
  .contact__role { margin-bottom: 8px; }
  .contact__address { margin-bottom: 8px; }
  .contact__list { list-style: none; }
  .contact__item { display: flex; align-items: center; gap: 8px; white-space: nowrap; }
  .contact__item svg { width: 13px; height: 13px; flex: none; fill: var(--brand-blue); }
  .contact__web-domain { color: var(--band-blue); }

  .band { position: absolute; left: 0; bottom: 0; width: 700px; height: 400px; }
</style>
</head>
<body>
  <section class="card card--front" aria-label="Card front">
    <div class="brand">
      <span class="brand__dot"></span>
      <span class="brand__name">Harborline Auto</span>
    </div>
  </section>

  <section class="card card--back" aria-label="Card back">
    <svg class="band" viewBox="0 0 700 400" aria-hidden="true">
      <path d="M0 400 L0 376 Q360 345 700 252 L700 400 Z" fill="var(--band-blue)"/>
      <path d="M120 358 Q420 318 700 238" fill="none" stroke="var(--accent-gold)" stroke-width="4"/>
    </svg>

    <div class="brand">
      <span class="brand__dot"></span>
      <span class="brand__name">Harborline Auto</span>
    </div>

    <div class="divider"></div>

    <div class="contact">
      <p class="contact__role">Car Dealer Customer Service</p>
      <p class="contact__address">2874 Cresthaven Road,<br>Larkmont, OH 45999</p>
      <ul class="contact__list">
        <li class="contact__item">
          <svg viewBox="0 0 24 24"><path d="M6.6 10.8a15 15 0 0 0 6.6 6.6l2.2-2.2c.3-.3.7-.4 1-.2 1.1.4 2.3.6 3.6.6.6 0 1 .4 1 1V20c0 .6-.4 1-1 1A17 17 0 0 1 3 4c0-.6.4-1 1-1h3.5c.6 0 1 .4 1 1 0 1.3.2 2.5.6 3.6.1.3 0 .7-.2 1z"/></svg>
          (555) 555-0148
        </li>
        <li class="contact__item">
          <svg viewBox="0 0 24 24"><path d="M3 8c0-2 4-4 9-4s9 2 9 4v2h-5V8H8v2H3zM6 12h12l2 8H4z"/></svg>
          (555) 555-0173
        </li>
        <li class="contact__item">
          <svg viewBox="0 0 24 24"><path d="M2 5h20v14H2zm2 2v.5l8 5 8-5V7z"/></svg>
          harborlineautoxq@mailnest.example
        </li>
        <li class="contact__item">
          <svg viewBox="0 0 24 24"><circle cx="12" cy="12" r="10"/><path d="M2 12h20M12 2c3 3 3 17 0 20M12 2c-3 3-3 17 0 20" stroke="#fff" stroke-width="1.5" fill="none"/></svg>
          <span>www.<span class="contact__web-domain">harborlineautoxq.net</span></span>
        </li>
      </ul>
    </div>
  </section>
</body>
</html>
```